Brochure for a civil enineering company in A4 format

I need a brochure design for our company TIRO Engineering S.r.l.. We are an engineering consultant company. Our main clients are from the infrastructure industry (geotechnical and underground sectors mainly).
We are looking for a 2 pages (4 faces) fold out design with a glued pocket where we can put individual data sheets.
I need A4 format pages.

Target Market(s)

We are an engineering consultant company. Our main clients are from the infrastructure industry (geotechnical and underground sectors mainly).

Industry/Entity Type

Civil Engineer

Font styles to use
Sans Serif

Requirements
Must have
• Overall: 2 pages in A4 format
Essential style. Bright and modern appearance.
Glued pocket
Logo integrated in a picture on the pocket where I would like to insert a slogan (… tiro engineering … reliable solutions …)
Attached are selected images which the designer can use and edit at their own discretion.
Some advice in the following (anyway designers are free to provide their solutions):
Outer sheets:
Front page with name, logo. It could be nice to have the “m” of the logo integrated in a pictures, also a modified picture (I mean modify one of the attached pictures) so to create a general image and do not tie the cover to a specific job.
Back page: offices address and contact email address. Nice to have one space for a slogan.
Inner sheet: text that I upload in the file “inside-sheets”, possibly with pictures on each sheet. In the right faces insert the glued pocket. On this pages insert the section OUR EXPERIENCE ….with a space for a picture of our team.
Nice to have
• Clean and essential design.
Pictures choosing from the atteched ones. Pictures could be modified in a very light manner to make them a general idea of the work ( I mean geotechnical world) without to be immediately linked to a specific site.
Should not have
• excessive frills

```html
<!DOCTYPE html>
<html lang="en">
<head>
<meta charset="utf-8">
<title>TIRO Engineering – Brochure Cover</title>
<link rel="stylesheet" href="https://fonts.googleapis.com/css2?family=Montserrat:wght@300;400;500;600;700&display=swap">
<style>
  :root{
    --stage:#686868;
    --paper:#f4f4f7;
    --paper-shade:#dcdce3;
    --ink:#1e1e20;
    --muted:#5b5b62;
    --band:#1f1f21;
    --band-text:#ffffff;
    --rule:#3a3a3d;
    --photo-sky:#4f83c4;
    --photo-steel:#b7b9bd;
    --photo-crane:#c8443c;
    --tunnel-deep:#2c2e5a;
    --tunnel-light:#6c72a8;
    --site-earth:#8c7a5c;
    --site-sky:#b9c7d6;
  }
  *{box-sizing:border-box;margin:0;padding:0}
  html,body{width:1200px;height:789px;overflow:hidden}
  body{background:var(--stage);font-family:'Montserrat',sans-serif;color:var(--ink);position:relative}

  .spread{position:absolute;left:105px;top:44px;width:990px;height:700px;display:flex;box-shadow:0 18px 40px rgba(0,0,0,.35)}
  .page{position:relative;width:495px;height:700px}
  .page--back{background:linear-gradient(160deg,var(--paper-shade) 0%,#ececf1 45%,var(--paper) 100%)}
  .page--front{background:linear-gradient(180deg,#fafafc 0%,var(--paper) 100%);box-shadow:inset 14px 0 18px -14px rgba(0,0,0,.18)}

  /* wordmark: invented name only, one colour, one weight */
  .brand-name{position:absolute;font-weight:600;letter-spacing:1px;color:var(--ink);line-height:1}
  .page--front .brand-name{left:0;right:0;top:46px;text-align:center;font-size:52px}
  .page--back .brand-name{left:372px;top:600px;font-size:36px}

  /* photo placeholders */
  .photo{position:absolute;border:5px solid #fff}
  .photo--lift{left:-60px;top:150px;width:296px;height:390px;border:none;
    background:linear-gradient(180deg,var(--photo-sky) 0%,#7ba6d8 40%,var(--photo-steel) 62%,var(--photo-crane) 78%,#7d6a55 100%)}
  .photo--tunnel{left:240px;top:112px;width:228px;height:205px;
    background:radial-gradient(ellipse at 55% 60%,var(--tunnel-light) 0%,var(--tunnel-deep) 65%,#1c1d3a 100%)}
  .photo--site{left:240px;top:312px;width:250px;height:185px;
    background:linear-gradient(180deg,var(--site-sky) 0%,#d8d4c4 35%,var(--site-earth) 60%,#6e5e45 100%)}

  /* front title */
  .cover-title{position:absolute;right:40px;top:556px;text-align:right}
  .cover-title__line{font-size:19px;font-weight:600;letter-spacing:.3px}
  .cover-title__band{display:inline-block;margin-top:6px;background:var(--band);color:var(--band-text);font-size:19px;font-weight:500;letter-spacing:.4px;padding:3px 26px 3px 30px}
  .cover-url{position:absolute;right:78px;top:640px;font-size:10px;letter-spacing:1px;color:var(--muted)}
  .cover-url b{font-weight:600;color:var(--ink)}

  /* back offices */
  .offices{position:absolute;left:38px;top:455px;width:260px}
  .offices__rule{height:1px;background:var(--rule);width:230px;margin-left:10px}
  .offices__title{font-size:17px;margin-top:8px;letter-spacing:.3px;font-weight:300}
  .offices__title strong{font-weight:600}
  .office{margin-top:14px;font-size:10.5px;line-height:1.45;font-weight:500}
  .office__row{display:grid;grid-template-columns:16px 1fr;align-items:center;column-gap:4px}
  .office__row svg{width:11px;height:11px}
  .office__city{font-weight:600}
  .offices__web{margin-top:14px}
</style>
</head>
<body>
  <main class="spread">
    <section class="page page--back" aria-label="Back page">
      <div class="offices">
        <div class="offices__rule"></div>
        <h2 class="offices__title">OUR <strong>OFFICES</strong></h2>

        <div class="office">
          <div class="office__row"><span></span><span class="office__city">Milano</span></div>
          <div class="office__row">
            <svg viewBox="0 0 12 12" fill="none" stroke="#1e1e20" stroke-width="1.2"><path d="M6 11S2.5 7 2.5 4.6a3.5 3.5 0 0 1 7 0C9.5 7 6 11 6 11z"/><circle cx="6" cy="4.6" r="1.2"/></svg>
            <span>Via Verdi, 14</span>
          </div>
          <div class="office__row"><span></span><span>20121 Milano - IT</span></div>
          <div class="office__row">
            <svg viewBox="0 0 12 12" fill="none" stroke="#1e1e20" stroke-width="1.2"><path d="M3 1.5l2 2.2-1.2 1.4a6 6 0 0 0 3.1 3.1L8.3 7l2.2 2-1.3 1.5C5.5 10.5 1.5 6.5 1.5 2.8z"/></svg>
            <span>+39 02 4455 6677</span>
          </div>
          <div class="office__row">
            <svg viewBox="0 0 12 12" fill="none" stroke="#1e1e20" stroke-width="1.1"><rect x="1.5" y="3" width="9" height="6.5"/><path d="M1.5 3l4.5 3.6L10.5 3"/></svg>
            <span>info@tiroengineering.example</span>
          </div>
        </div>

        <div class="office">
          <div class="office__row"><span></span><span class="office__city">Arco TN</span></div>
          <div class="office__row">
            <svg viewBox="0 0 12 12" fill="none" stroke="#1e1e20" stroke-width="1.2"><path d="M6 11S2.5 7 2.5 4.6a3.5 3.5 0 0 1 7 0C9.5 7 6 11 6 11z"/><circle cx="6" cy="4.6" r="1.2"/></svg>
            <span>Via Roma, 12</span>
          </div>
          <div class="office__row"><span></span><span>38062 Arco TN - IT</span></div>
          <div class="office__row">
            <svg viewBox="0 0 12 12" fill="none" stroke="#1e1e20" stroke-width="1.2"><path d="M3 1.5l2 2.2-1.2 1.4a6 6 0 0 0 3.1 3.1L8.3 7l2.2 2-1.3 1.5C5.5 10.5 1.5 6.5 1.5 2.8z"/></svg>
            <span>+39 02 4455 6677</span>
          </div>
          <div class="office__row">
            <svg viewBox="0 0 12 12" fill="none" stroke="#1e1e20" stroke-width="1.1"><rect x="1.5" y="3" width="9" height="6.5"/><path d="M1.5 3l4.5 3.6L10.5 3"/></svg>
            <span>info@tiroengineering.example</span>
          </div>
        </div>

        <div class="office offices__web">
          <div class="office__row">
            <svg viewBox="0 0 12 12" fill="none" stroke="#1e1e20" stroke-width="1"><circle cx="6" cy="6" r="4.5"/><ellipse cx="6" cy="6" rx="2" ry="4.5"/><path d="M1.5 6h9"/></svg>
            <span>www.tiroengineering.example</span>
          </div>
        </div>
      </div>

      <span class="brand-name">tiro</span>
    </section>

    <section class="page page--front" aria-label="Front page">
      <span class="brand-name">tiro</span>

      <div class="photo photo--lift" role="img" aria-label="Photo of a large crane lifting a tunnel boring machine shield on a construction site under a blue sky"></div>
      <div class="photo photo--tunnel" role="img" aria-label="Photo of twin lit tunnel bores under construction underground"></div>
      <div class="photo photo--site" role="img" aria-label="Photo of tunnel portals being excavated into an earthen hillside with a drilling rig"></div>

      <div class="cover-title">
        <div class="cover-title__line">LOREM IPSUM DOLOR SIT AMET</div>
        <div class="cover-title__band">CONSECTETUR ADIPISCING</div>
      </div>
      <div class="cover-url">www.<b>TiroEngineering</b>.example</div>
    </section>
  </main>
</body>
</html>
```